Retail Jewelry Business Card Design Project

We are in need of a new business card design for a retail jewelry store. This store is in the business of fine jewelry including but not specific to bridal jewelry, diamonds, designer jewelry and watches.

This store has been in business for 20 years but continues to strive for a modern professional appeal. The main colors use for this business are a royal blue, white and silver.

Target Market(s)

Target market is ages 18-50

Industry/Entity Type

Jewelry

Requirements
Must have
• Sales Person Name
Sales Person Email Address

Store Address
Store Phone
Website

Standard business card size. No odd shapes or sizes.
Nice to have
• Overall modern feel for card.

We have thought that a design with a nice feature of the logo on the back of the card would be nice but open to ideas.
Should not have
• No specific images of jewelry should be used.

```html
<!DOCTYPE html>
<html lang="en">
<head>
<meta charset="utf-8">
<title>Marlow Reed Fine Jewelry – Business Cards</title>
<link href="https://fonts.googleapis.com/css2?family=Open+Sans:wght@400;600&display=swap" rel="stylesheet">
<style>
  :root {
    --page-bg: #ffffff;
    --navy-deep: #0f1424;
    --navy-mid: #131b33;
    --royal-blue: #2e2e8f;
    --lavender: #7a72c2;
    --ink: #333333;
    --ink-soft: #444444;
    --white: #ffffff;
    --shadow: rgba(0, 0, 0, 0.35);
  }
  * { margin: 0; padding: 0; box-sizing: border-box; }
  html, body {
    width: 1200px; height: 1000px; overflow: hidden;
    background: var(--page-bg);
    font-family: "Open Sans", Arial, sans-serif;
  }
  .stage { position: relative; width: 1200px; height: 1000px; }

  .card {
    position: absolute; left: 285px; width: 653px; height: 373px;
    border-radius: 22px; overflow: hidden;
    box-shadow: 3px 5px 8px var(--shadow);
  }
  .card--front {
    top: 103px;
    background: linear-gradient(135deg, var(--navy-mid) 0%, var(--navy-deep) 100%);
  }
  .card--back { top: 533px; background: var(--white); }

  .brand { position: absolute; font-weight: 600; line-height: 1.1; }
  .brand__name { display: block; }
  .brand__tag { display: block; letter-spacing: 0.12em; }

  .card--front .brand { left: 55px; top: 268px; color: var(--white); }
  .card--front .brand__name { font-size: 38px; }
  .card--front .brand__tag { font-size: 16px; margin-top: 8px; padding-left: 38px; }

  .card--back .brand { left: 47px; top: 60px; color: var(--royal-blue); }
  .card--back .brand__name { font-size: 46px; }
  .card--back .brand__tag { font-size: 19px; margin-top: 8px; padding-left: 46px; }

  .website {
    position: absolute; right: 46px; color: var(--white);
    font-size: 15px; letter-spacing: 0.03em;
  }
  .card--front .website { top: 314px; }
  .card--back .website { top: 342px; right: 43px; z-index: 2; }

  .address {
    position: absolute; left: 47px; top: 217px;
    font-size: 15px; line-height: 22px; color: var(--ink); font-style: normal;
  }
  .contact-list { position: absolute; left: 47px; top: 273px; list-style: none; }
  .contact-list li {
    display: flex; align-items: center; gap: 9px;
    font-size: 15px; line-height: 22px; color: var(--ink);
  }
  .contact-list svg { width: 16px; height: 12px; fill: var(--lavender); }

  .person { position: absolute; right: 43px; top: 211px; text-align: right; }
  .person__name { font-size: 19px; font-weight: 600; color: var(--royal-blue); }
  .person__name .surname { color: var(--lavender); }
  .person__role { font-size: 15px; color: var(--ink-soft); margin-top: 1px; }

  .swoosh { position: absolute; left: 0; bottom: 0; width: 653px; height: 373px; }
</style>
</head>
<body>
<main class="stage">

  <section class="card card--front" aria-label="Card front">
    <div class="brand">
      <span class="brand__name">Marlow Reed</span>
      <span class="brand__tag">FINE JEWELRY</span>
    </div>
    <p class="website">www.marlowreedjewelry.com</p>
  </section>

  <section class="card card--back" aria-label="Card back">
    <div class="brand">
      <span class="brand__name">Marlow Reed</span>
      <span class="brand__tag">FINE JEWELRY</span>
    </div>

    <address class="address">2280 Larkin Street<br>Bayview, FL 32999</address>

    <ul class="contact-list">
      <li>
        <svg viewBox="0 0 16 12" aria-hidden="true"><path d="M1 4 Q8 -1 15 4 L13 5.5 L11 4.5 L11 3.5 Q8 2.5 5 3.5 L5 4.5 L3 5.5 Z M4 6 L12 6 L14 11 L2 11 Z"/></svg>
        000.000.0000
      </li>
      <li>
        <svg viewBox="0 0 16 12" aria-hidden="true"><path d="M0 0 H16 V12 H0 Z M1.5 1.5 L8 7 L14.5 1.5 Z"/></svg>
        marlow@marlowreedjewelry.com
      </li>
    </ul>

    <div class="person">
      <p class="person__name">Marlow Reed <span class="surname">Ashby</span></p>
      <p class="person__role">Owner</p>
    </div>

    <svg class="swoosh" viewBox="0 0 653 373" aria-hidden="true">
      <defs>
        <linearGradient id="bandGrad" x1="0" y1="0" x2="1" y2="0">
          <stop offset="0" stop-color="#1a1f3a"/>
          <stop offset="1" stop-color="#0d1020"/>
        </linearGradient>
      </defs>
      <path d="M205 373 C270 338 380 326 475 328 C390 333 300 348 245 373 Z" fill="var(--royal-blue)"/>
      <path d="M255 373 C340 340 480 322 653 316 L653 373 Z" fill="url(#bandGrad)"/>
    </svg>
    <p class="website">www.marlowreedjewelry.com</p>
  </section>

</main>
</body>
</html>
```